Harbor Loom Floors Letterhead

Letterhead used for business reasons. It must be editable and easy to use.

Address is 2715 W. Pelican Lane Englewood FL 34187 - 941.382.6519

```html
<!DOCTYPE html>
<html lang="en">
<head>
<meta charset="utf-8">
<title>Harbor Loom Floors Letterhead</title>
<link href="https://fonts.googleapis.com/css2?family=Open+Sans:wght@400;600&family=Lexend:wght@500&family=Lato:wght@400&display=swap" rel="stylesheet">
<style>
  :root {
    --orange: #e08a24;
    --taupe: #978d88;
    --ink: #2b2b2b;
    --body: #6f6f6f;
    --muted: #555;
    --pattern: #f3f3f3;
    --backdrop: #e9eaec;
    --paper: #ffffff;
  }
  * { margin: 0; padding: 0; box-sizing: border-box; }
  html, body { width: 999px; height: 1200px; overflow: hidden; background: var(--backdrop); }
  body { position: relative; font-family: "Open Sans", sans-serif; }

  .letterhead {
    position: absolute; left: 89px; top: 25px;
    width: 820px; height: 1150px;
    background: var(--paper); overflow: hidden;
  }
  .page-art { position: absolute; inset: 0; width: 820px; height: 1150px; }

  .brand-name {
    position: absolute; left: 76px; top: 104px;
    font-family: "Open Sans", sans-serif; font-weight: 600;
    font-size: 34px; line-height: 40px; color: var(--orange);
  }

  .sender { position: absolute; left: 73px; top: 272px; }
  .sender-name { font-size: 22px; font-weight: 600; color: var(--orange); line-height: 28px; }
  .sender-role { font-size: 11.5px; color: var(--muted); margin-top: 2px; }

  .contact-list { position: absolute; left: 73px; top: 336px; list-style: none; }
  .contact-list li { font-size: 14px; line-height: 23px; color: var(--muted); }
  .contact-list b { display: inline-block; width: 29px; color: var(--orange); font-weight: 600; }

  .letter-date {
    position: absolute; right: 75px; top: 393px;
    font-size: 14px; color: var(--muted);
  }

  .letter-body { position: absolute; left: 74px; top: 456px; width: 671px; }
  .letter-body p {
    font-size: 14.2px; line-height: 21.6px; color: var(--body);
    text-align: justify; margin-bottom: 21.6px;
  }

  .signature {
    position: absolute; left: 613px; top: 820px; width: 120px; height: 76px;
    background: linear-gradient(135deg, #f4f4f4, #e8e8e8); border-radius: 4px;
  }
  .signer-name {
    position: absolute; right: 75px; top: 906px;
    font-family: "Lexend", sans-serif; font-weight: 500; font-size: 19px; color: var(--ink);
  }

  .footer-contact { position: absolute; right: 75px; top: 972px; list-style: none; text-align: right; }
  .footer-contact li {
    display: flex; justify-content: flex-end; align-items: center; gap: 4px;
    font-family: "Lato", sans-serif; font-size: 12px; color: var(--body); line-height: 25px;
  }
  .footer-contact svg { width: 16px; height: 16px; }
</style>
</head>
<body>
<main class="letterhead">
  <svg class="page-art" viewBox="0 0 820 1150" aria-hidden="true">
    <polygon points="0,0 423,0 399,28 0,28" fill="var(--orange)"/>
    <polygon points="338,1090 820,1090 820,1114 314,1114" fill="var(--taupe)"/>
    <polygon points="297,1114 820,1114 820,1150 266,1150" fill="var(--orange)"/>
  </svg>
  <svg class="page-art" viewBox="0 0 820 1150" role="img" aria-label="Faint decorative diamond line pattern">
    <polygon points="0,1002 126,876 325,1075 250,1150 0,1150" fill="var(--pattern)"/>
  </svg>

  <div class="brand-name">Harbor Loom<br>Floors</div>

  <section class="sender">
    <h1 class="sender-name">Nora Whitfield</h1>
    <p class="sender-role">Chief Director</p>
  </section>

  <ul class="contact-list">
    <li><b>A :</b>1190 Tidewater Avenue, Tampa, FL 33602</li>
    <li><b>W :</b>www.harborloomfloors.com</li>
    <li><b>P :</b>+1 941 555 0142</li>
    <li><b>M :</b>hello@harborloomfloors.com</li>
  </ul>

  <p class="letter-date">12 December, 2025</p>

  <article class="letter-body">
    <p>Lorem ipsum dolor sit amet, consectetuer adipiscing elit, sed diam nonummy nibh euismod tincidunt ut laoreet dolore magna aliquam erat volutpat. Ut wisi enim ad minim veniam, quis nostrud exerci tation ullamcorper suscipit lobortis nisl ut aliquip ex ea commodo consequat. Duis autem vel eum iriure dolor in hendrerit in vulputate velit esse molestie consequat, vel illum dolore eu feugiat nulla facilisis at vero eros et accumsan et iusto odio dignissim qui blandit praesent luptatum zzril delenit augue duis dolore te feugait nulla facilisi.</p>
    <p>Lorem ipsum dolor sit amet, cons ectetuer adipiscing elit, sed diam nonummy nibh euismod tincidunt ut laoreet dolore magna aliquam erat volutpat. Ut wisi enim ad minim veniam, quis nostrud exerci tation ullamcorper suscipit lobortis nisl ut aliquip ex ea commodo consequat.</p>
    <p>Lorem ipsum dolor sit amet, consectetuer adipiscing elit, sed diam nonummy nibh euismod tincidunt ut laoreet dolore magna aliquam eratveniam, quis nostrud exerci tation ullamcorper suscipit lobortis nisl ut aliquip ex ea commodo consequat. Lorem ipsum dolor sit zamet, consectetuer adipiscing elit, sed diam nonummy nibh euismod tincidunt.</p>
  </article>

  <div class="signature" role="img" aria-label="Handwritten signature"></div>
  <p class="signer-name">Mr. Elias Marsh</p>

  <ul class="footer-contact">
    <li>941.382.6519
      <svg viewBox="0 0 16 16" aria-hidden="true"><rect width="16" height="16" rx="2" fill="var(--orange)"/><path d="M5 3.5l2 2-1.2 1.3a6 6 0 0 0 3.4 3.4L10.5 9l2 2-1.3 1.5C7.5 12.3 3.7 8.5 3.5 4.8z" fill="#fff"/></svg>
    </li>
    <li>2715 W. Pelican Lane Englewood FL 34187
      <svg viewBox="0 0 16 16" aria-hidden="true"><rect width="16" height="16" rx="2" fill="var(--orange)"/><path d="M8 2.8a3.7 3.7 0 0 0-3.7 3.7C4.3 9.3 8 13.2 8 13.2s3.7-3.9 3.7-6.7A3.7 3.7 0 0 0 8 2.8z" fill="#fff"/><circle cx="8" cy="6.5" r="1.4" fill="var(--orange)"/></svg>
    </li>
  </ul>
</main>
</body>
</html>
```